Counseling Practice Business Card

I need a professional looking business card incorporating my new logo that was just completed. Card needs to incorporate my name and title, description of my specialty, my address, my phone number, my fax number, my email and my website URL. I need to be able to choose design on/with different paper colors and textures.
I do not have a lot of business card ideas so I am open to anything but I want bold,sharp, clear card without additional designs other than my logo (see attached file info). I am open to different color backgrounds or paper colors including black. I do not like traditional brackets around area codes in phone number or dashes between numbers in phone number. Am open to other ways of presenting including periods between numbers as appropriate. I do not know enough to know what I like yet but I want card to coordinate and work together with my logo. My practice emphasizes natural mental health interventions so any use of color (with background paper color or the blue and green in my logo) that elicits nature is nice. In addition to black, any natural brown or wood looking background might be desirable also. Most of the offerings so far look very similar and boring.

Target Market(s)

Potential therapy clients and other professionals

Contact Information for Business Card

Card information:
Gerald M. Whitcombe, Ph.D.
Licensed Clinical Psychologist
Integrative Health Coach
4812 Marlowe Ridge Blvd SE
Suite 310
Duluth, GA 30096
(770) 415-2983 phone
(770) 581-4096 fax
drgeraldwhitcombe@quillmarsh.net
brightfernwellness.net

Font styles to use
Serif
Sans Serif
Other font styles liked:
• anything that you think looks crisp, clear and easily readable

Requirements
Must have
• Any color used should coordinate with my logo design (see attached files).
• Card should be printed horizontally so top and bottom are longest sides of rectangle.
• Background color or paper color should complement and highlight logo. Do not like a white background. black, grey, brown or any color my logo would blend well with.
Nice to have
• I would like designer to utilize color to highlight letters/name or phone-fax-web symbols.
• Bottom edge of card could be highlighted if appropriate to an idea.
Should not have
• I would NOT want the card to have a pure white background at all.
• No clear cards.
• Cards should be oriented with long sides on bottom and top, NOT sides. DO NOT LIKE THIS THIN TALL ORIENTATION.

```html
<!DOCTYPE html>
<html lang="en">
<head>
<meta charset="utf-8">
<title>Brightfern Wellness Business Card</title>
<link rel="stylesheet" href="https://fonts.googleapis.com/css2?family=Roboto+Condensed:wght@400;700&display=swap">
<style>
  :root {
    --stage: #e9e6e1;
    --card-black: #131417;
    --brand-blue: #2a73b8;
    --brand-green: #1e6b3a;
    --text-light: #ffffff;
  }
  * { margin: 0; padding: 0; box-sizing: border-box; }
  html, body { width: 1200px; height: 960px; overflow: hidden; }
  body {
    background: var(--stage);
    font-family: "Roboto Condensed", Arial, sans-serif;
    position: relative;
  }
  .card {
    position: absolute;
    width: 600px;
    height: 342px;
    background: var(--card-black);
    overflow: hidden;
  }
  .card--front { left: 314px; top: 113px; }
  .card--back  { left: 312px; top: 472px; }

  .card__shape { position: absolute; inset: 0; }

  .identity {
    position: absolute;
    top: 42px;
    left: 0;
    width: 600px;
    text-align: center;
  }
  .identity__name {
    color: var(--brand-blue);
    font-weight: 700;
    font-size: 21px;
    text-transform: uppercase;
    letter-spacing: 0.2px;
    line-height: 1.2;
  }
  .identity__title {
    color: var(--brand-green);
    font-size: 15px;
    line-height: 19px;
  }

  .brand-name {
    position: absolute;
    left: 0;
    width: 100%;
    text-align: center;
    font-weight: 700;
    white-space: nowrap;
  }
  .card--front .brand-name {
    top: 168px;
    left: 100px;
    width: 400px;
    font-size: 38px;
    color: var(--text-light);
  }
  .card--back .brand-name {
    top: 135px;
    font-size: 52px;
    color: var(--brand-blue);
  }

  .contact {
    position: absolute;
    top: 248px;
    left: 100px;
    width: 400px;
    text-align: center;
    color: var(--text-light);
    font-size: 13.5px;
    line-height: 21px;
    white-space: nowrap;
  }
</style>
</head>
<body>
  <section class="card card--front" aria-label="Business card front">
    <svg class="card__shape" width="600" height="342" viewBox="0 0 600 342" aria-hidden="true">
      <path fill="var(--brand-blue)" d="M0 240 C 20 290, 70 325, 125 342 L 0 342 Z"/>
      <path fill="var(--brand-blue)" d="M600 174 C 520 136, 400 114, 280 126 C 150 138, 40 180, 46 236 C 52 292, 120 330, 160 342 L 600 342 Z"/>
    </svg>
    <header class="identity">
      <h1 class="identity__name">Gerald M. Whitcombe, Ph.D.</h1>
      <p class="identity__title">Licensed Clinical Psychologist</p>
      <p class="identity__title">Integrative Health Coach</p>
    </header>
    <p class="brand-name">Brightfern Wellness</p>
    <address class="contact" style="font-style: normal;">
      <p>4812 Marlowe Ridge Blvd SE, Suite 310, Duluth, GA 30096</p>
      <p>P: (770) 415-2983 F: (770) 581-4096 drgeraldwhitcombe@quillmarsh.net</p>
      <p>www.brightfernwellness.net</p>
    </address>
  </section>

  <section class="card card--back" aria-label="Business card back">
    <p class="brand-name">Brightfern Wellness</p>
  </section>
</body>
</html>
```